Modern business card design for professional copywriter

I'd like a business card design that I can use to have my cards printed out by quillprint.com as a squared corners business card (see artwork and design guidelines here: https://help.quillprint.com/hc/en-gb/sections/200570950-QUILL-Product-Templates)

The design should be clean and modern and reflect the colours, tone and branding on my website: https://tessavorrin.com.au

Target Market(s)

Professionals, B2B small business owners

Industry/Entity Type

Business

Contact Information for Business Card

Tessa Vorrin
m: 0468 905 327
e: tessa@tessavorrin.com.au
w: tessavorrin.com.au

Font styles to use
Sans Serif

Requirements
Must have
• Tagline: "Smart copywriting for clever business people"
• Brand colours: fd8000, 009984, 666666 and black
Nice to have

```html
<!DOCTYPE html>
<html lang="en">
<head>
<meta charset="utf-8">
<title>Tessa Vorrin – Business Card</title>
<link href="https://fonts.googleapis.com/css2?family=Montserrat:wght@400;500;700&display=swap" rel="stylesheet">
<style>
  :root {
    --orange: #fd8000;
    --teal: #009984;
    --grey: #666666;
    --black: #000000;
    --white: #ffffff;
    --backdrop: #a7a8ab;
  }
  * { margin: 0; padding: 0; box-sizing: border-box; }
  html, body { width: 1200px; height: 936px; overflow: hidden; }
  body {
    background: var(--backdrop);
    font-family: "Montserrat", sans-serif;
    position: relative;
  }
  .card {
    position: absolute;
    left: 264px;
    width: 661px;
    height: 378px;
    background: var(--white);
    border-radius: 16px;
    overflow: hidden;
  }
  .card--front { top: 72px; }
  .card--back { top: 497px; }

  .brand {
    position: absolute;
    display: flex;
    align-items: center;
    gap: 10px;
    color: var(--teal);
    font-weight: 500;
    font-size: 30px;
    letter-spacing: -0.3px;
    white-space: nowrap;
  }
  .brand__dot {
    width: 16px; height: 16px;
    border-radius: 50%;
    background: var(--orange);
  }
  .card--front .brand { right: 39px; top: 104px; }
  .card--back .brand { left: 50%; top: 158px; transform: translateX(-50%); }

  .holder-name {
    position: absolute;
    left: 51px; top: 216px;
    font-size: 29px;
    font-weight: 700;
    color: var(--black);
  }
  .divider {
    position: absolute;
    left: 51px; top: 269px;
    width: 562px; height: 2px;
    background: var(--grey);
  }
  .contact {
    position: absolute;
    left: 50px; top: 284px;
    list-style: none;
  }
  .contact__item {
    display: flex;
    align-items: center;
    height: 22.5px;
    font-size: 19px;
    color: var(--black);
  }
  .contact__icon { width: 17px; height: 17px; margin-right: 16px; flex: none; }
  .contact__muted { color: var(--grey); }

  .tagline-band {
    position: absolute;
    left: 0; top: 315px;
    width: 100%; height: 40px;
    background: var(--grey);
  }
  .tagline {
    position: absolute;
    left: 38px; top: 310px;
    width: 588px; height: 50px;
    border: 5px solid var(--white);
    border-radius: 25px;
    background: var(--grey);
    color: var(--white);
    font-size: 18px;
    letter-spacing: 0.6px;
    display: flex;
    align-items: center;
    justify-content: center;
  }
</style>
</head>
<body>

<section class="card card--front" aria-label="Card front">
  <div class="brand"><span class="brand__dot"></span>Tessa Vorrin</div>
  <h1 class="holder-name">Tessa Vorrin</h1>
  <div class="divider"></div>
  <ul class="contact">
    <li class="contact__item">
      <svg class="contact__icon" viewBox="0 0 20 20" aria-hidden="true">
        <circle cx="10" cy="10" r="10" fill="#000"/>
        <rect x="6.5" y="4" width="7" height="12" rx="1.2" fill="#fff"/>
        <rect x="7.7" y="5.5" width="4.6" height="7.5" fill="#000"/>
      </svg>0468 905 327
    </li>
    <li class="contact__item">
      <svg class="contact__icon" viewBox="0 0 20 20" aria-hidden="true">
        <circle cx="10" cy="10" r="10" fill="#000"/>
        <rect x="5" y="6.5" width="10" height="7" fill="#fff"/>
        <path d="M5 6.5 L10 10.5 L15 6.5" fill="none" stroke="#000" stroke-width="1.2"/>
      </svg>tessa@<span class="contact__muted">tessavorrin</span>.com.au
    </li>
    <li class="contact__item">
      <svg class="contact__icon" viewBox="0 0 20 20" aria-hidden="true">
        <circle cx="10" cy="10" r="10" fill="#000"/>
        <g fill="none" stroke="#fff" stroke-width="1.1">
          <circle cx="10" cy="10" r="5.5"/>
          <ellipse cx="10" cy="10" rx="2.4" ry="5.5"/>
          <line x1="4.5" y1="10" x2="15.5" y2="10"/>
          <line x1="5.3" y1="7.3" x2="14.7" y2="7.3"/>
          <line x1="5.3" y1="12.7" x2="14.7" y2="12.7"/>
        </g>
      </svg>tessavorrin.com.au
    </li>
  </ul>
</section>

<section class="card card--back" aria-label="Card back">
  <div class="brand"><span class="brand__dot"></span>Tessa Vorrin</div>
  <div class="tagline-band"></div>
  <p class="tagline">"Smart copywriting for clever business people"</p>
</section>

</body>
</html>
```